Norrell Advisory WA Business Card

Create an interesting, eye catching and colourful two sided business card. We are a business consulting operation assisting SME's improve all areas of their business. We provide consulting services to assist SME's to create a culture of continuous improvement, making a positive difference in the business. Our tag line is Small changes, big rewards. We want to create a well recognised, innovative brand that can be continued throughout our website, social media and email correspondence.

Target Market(s)

Small to Medium Enterprise Business Owners

Industry/Entity Type

Business Consultant

Contact Information for Business Card

Name of Business: Norrell Advisory - Steady Steps Strong Results
Derek Holloway Ph 0407385510 Megan Holloway Ph 0407913847
Email norrelladvisorywa@mailbox-example.com
Web address TBA
FaceBook page TBA

BACKSIDE OF CARD

Providing assistance with:

• Organisation & Efficiency
• Revenue generation & Marketing
• Financial Management
• Production quality & delivery
• Systems & Process documentation
• Exit Strategy

Font styles to use
Other font styles liked:
• Calibri

Colors

Designer to choose colors to be used in the design.

Requirements
Must have
• Calibri font

```html
<!DOCTYPE html>
<html lang="en">
<head>
<meta charset="utf-8">
<title>Norrell Advisory WA Business Card</title>
<link href="https://fonts.googleapis.com/css2?family=Carlito:wght@400;700&display=swap" rel="stylesheet">
<style>
  :root {
    --stage: #262626;
    --card: #1b1b1c;
    --card-edge: #2c2c2e;
    --blue: #3d86c9;
    --red: #de4430;
    --white: #f2f2f2;
    --emboss: #a9a9ab;
    --emboss-soft: #7d7d80;
    --mark-dark: #0e0e0f;
  }
  * { box-sizing: border-box; margin: 0; padding: 0; }
  html, body {
    width: 1200px; height: 900px; overflow: hidden;
    background: var(--stage);
    font-family: "Carlito", "Calibri", sans-serif;
  }
  .canvas { position: relative; width: 1200px; height: 900px; }
  .card {
    position: absolute; left: 240px; width: 720px; height: 400px;
    background: linear-gradient(135deg, var(--card) 0%, var(--card-edge) 100%);
    box-shadow: 0 10px 30px rgba(0,0,0,.45);
  }
  .card--front { top: 40px; }
  .card--back { top: 460px; }

  /* front */
  .brand { position: absolute; display: flex; align-items: center; gap: 18px; }
  .card--front .brand { left: 190px; top: 150px; }
  .brand__square { width: 70px; height: 70px; flex: none; }
  .card--front .brand__square { background: var(--mark-dark); }
  .brand__name { font-weight: 700; font-size: 36px; letter-spacing: 1px; line-height: 1; white-space: nowrap; }
  .brand__tagline { font-size: 19px; letter-spacing: 1.2px; margin-top: 4px; white-space: nowrap; }
  .card--front .brand__name { color: var(--emboss); }
  .card--front .brand__tagline { color: var(--emboss-soft); }

  /* back */
  .card--back .brand { left: 40px; top: 150px; }
  .card--back .brand__square { width: 62px; height: 62px; background: var(--blue); }
  .card--back .brand__name { color: var(--blue); font-size: 32px; }
  .card--back .brand__tagline { color: var(--red); font-size: 17px; }
  .divider { position: absolute; left: 372px; top: 30px; width: 3px; height: 300px; background: var(--blue); }
  .details { position: absolute; left: 400px; top: 28px; right: 20px; color: var(--white); }
  .partners { color: var(--blue); font-weight: 700; font-size: 27px; letter-spacing: 1px; line-height: 1.1; text-transform: uppercase; }
  .contacts { list-style: none; margin-top: 12px; font-size: 16px; line-height: 1.35; }
  .contacts li { display: flex; align-items: center; gap: 9px; white-space: nowrap; }
  .contacts svg { width: 11px; height: 11px; flex: none; }
  .web__domain { color: var(--red); font-weight: 700; }
  .services { list-style: none; margin-top: 12px; font-size: 17px; line-height: 1.3; }
  .services li::before { content: "> "; color: var(--blue); }
</style>
</head>
<body>
<main class="canvas">
  <section class="card card--front" aria-label="Card front">
    <div class="brand">
      <span class="brand__square"></span>
      <div>
        <p class="brand__name">Norrell Advisory</p>
        <p class="brand__tagline">Steady Steps Strong Results</p>
      </div>
    </div>
  </section>

  <section class="card card--back" aria-label="Card back">
    <div class="brand">
      <span class="brand__square"></span>
      <div>
        <p class="brand__name">Norrell Advisory</p>
        <p class="brand__tagline">Steady Steps Strong Results</p>
      </div>
    </div>
    <span class="divider"></span>
    <div class="details">
      <p class="partners">Derek Holloway<br>Megan Holloway</p>
      <ul class="contacts">
        <li><svg viewBox="0 0 12 12"><path d="M3 1 L5 3 L4 4.5 Q5.5 7 7.5 8 L9 7 L11 9 L9.5 11 Q4 10 1 3 Z" fill="var(--blue)"/></svg><span>0407385510</span></li>
        <li><svg viewBox="0 0 12 12"><path d="M3 1 L5 3 L4 4.5 Q5.5 7 7.5 8 L9 7 L11 9 L9.5 11 Q4 10 1 3 Z" fill="var(--blue)"/></svg><span>0407913847</span></li>
        <li><svg viewBox="0 0 12 12"><rect x="1" y="3" width="10" height="7" fill="none" stroke="var(--blue)" stroke-width="1.2"/><path d="M1 3 L6 7 L11 3" fill="none" stroke="var(--blue)" stroke-width="1.2"/></svg><span>norrelladvisorywa@mailbox-example.com</span></li>
        <li><svg viewBox="0 0 12 12"><circle cx="6" cy="6" r="5" fill="none" stroke="var(--blue)" stroke-width="1.2"/><ellipse cx="6" cy="6" rx="2.2" ry="5" fill="none" stroke="var(--blue)" stroke-width="1"/><line x1="1" y1="6" x2="11" y2="6" stroke="var(--blue)" stroke-width="1"/></svg><span>www.<span class="web__domain">norrelladvisorywa</span>.com</span></li>
      </ul>
      <ul class="services">
        <li>Organisation &amp; Efficiency</li>
        <li>Revenue generation &amp; Marketing</li>
        <li>Financial Management</li>
        <li>Production quality &amp; delivery</li>
        <li>Systems &amp; Process documentation</li>
        <li>Exit Strategy</li>
      </ul>
    </div>
  </section>
</main>
</body>
</html>
```